VORNAK SYSTEMS BUSINESS CARD DESIGN

WE WANT COMPLETE NEW DESIGN OF OUR BUSINESS CARD. WE ARE AN INTEGRATION COMPANY, WHERE WE INTEGRATE IOT/SMART SYSTEMS TO HOMES AND CORPORATE CUSTOMERS. WE SUPPLY AND INSTALL AUTOMATION PRODUCTS. THE FINAL DESIGN SHOULD COMMUNICATE TECHNOLOGY. THE CARD DESIGN SHOULD BE VERY IMPACT FULL. LOGO NEEDS TO BE THERE. IT WOULD NICE IF THE DESIGN WAS CLEAN. COLORS IS UP TO DESIGNER TO PLAY WITH, OR CAN STICK TO CORPORATE COLORS (FOLLOW LOGO). I HAVE ADDED FEW REFERENCE PHOTOS TO DRAW INSPIRATION MAYBE. I HAVE ADDED A HEX DESIGN, ITS NOT NECESSARY TO USE THIS DESIGN, ITS UPTO DESIGNER, JUST ADDED IF NEEDED TO PLAY WITH DESIGN.

Target Market(s)

Private end users and corporate clients

Industry/Entity Type

technology, home automation, home theaters, building management systems, IOT

Contact Information for Business Card

It should include Employee name, personal number, office number, email address, both in English and arabic. DETAILS TO INCLUDE :RAJESH PALLIVAL, MOBILE 0097150738265,OFFCIE 009714368547, RAJESH@VORNAKSYS.EXAMPLE

Requirements
Must have
• Should feel like a technology company from design. Details both and in English and arabic (or at least have provision for arabic in design).
Nice to have
• I would like logo on one side, and details on the other side. Logo design side should communicate technology with logo. Other side can be clean just with information or also have some design aspects following from logo side. it would be interesting to see submissions with square design as well (that looks like an app Icon). colors could be of logo, red black grey and white. I have added some designs to draw inspiration from

```html
<!DOCTYPE html>
<html lang="en">
<head>
<meta charset="utf-8">
<title>Vornak Systems – Business Card</title>
<link rel="stylesheet" href="https://fonts.googleapis.com/css2?family=Roboto+Condensed:wght@700&family=Roboto:wght@400&family=Michroma&display=swap">
<style>
  :root {
    --backdrop: #2c2c2c;
    --card: #ececec;
    --ink: #0d0d0d;
    --grey: #8a8a8a;
    --red: #c8161d;
    --mosaic: linear-gradient(120deg, #1fa37a 0%, #2bd0e0 22%, #f4d21a 42%, #e8731c 60%, #d41431 78%, #2a1d6b 100%);
  }
  * { margin: 0; padding: 0; box-sizing: border-box; }
  html, body { width: 1200px; height: 1138px; overflow: hidden; }
  body { background: var(--backdrop); position: relative; font-family: "Roboto", Arial, sans-serif; color: var(--ink); }

  .card {
    position: absolute; width: 620px; height: 376px;
    background: var(--card); border-radius: 14px; overflow: hidden;
  }
  .card--front { left: 272px; top: 184px; }
  .card--back  { left: 274px; top: 606px; }

  .brand { position: absolute; display: flex; align-items: center; gap: 10px; z-index: 1; }
  .brand__dot { border-radius: 50%; background: var(--red); flex: none; }
  .brand__name {
    font-family: "Roboto Condensed", "Arial Narrow", sans-serif; font-weight: 700;
    color: var(--ink); letter-spacing: 1px; line-height: 1; white-space: nowrap;
  }
  .card--front .brand { left: 48px; top: 110px; }
  .card--front .brand__dot { width: 26px; height: 26px; }
  .card--front .brand__name { font-size: 28px; }

  .tagline {
    position: absolute; font-family: "Michroma", "Arial", sans-serif;
    font-size: 11px; letter-spacing: 1.5px; white-space: nowrap; z-index: 1;
  }
  .card--front .tagline { left: 46px; top: 154px; color: var(--ink); }

  .mosaic-disc {
    position: absolute; left: 334px; top: 54px; width: 268px; height: 268px;
    border-radius: 50%; background: var(--mosaic);
  }

  .card--back .brand { left: 30px; top: 46px; gap: 16px; }
  .card--back .brand__dot { width: 56px; height: 56px; }
  .card--back .brand__name { font-size: 58px; letter-spacing: 4px; }

  .person {
    position: absolute; left: 36px; top: 224px;
    font-family: "Roboto Condensed", "Arial Narrow", sans-serif; font-weight: 700;
    font-size: 26px; color: var(--red);
  }
  .contacts { position: absolute; list-style: none; font-size: 17px; }
  .contacts li { display: flex; align-items: center; gap: 14px; height: 24px; white-space: nowrap; }
  .contacts svg { width: 16px; height: 16px; flex: none; }
  .contacts--phones { left: 36px; top: 288px; }
  .contacts--web { left: 304px; top: 230px; }

  .footer-band {
    position: absolute; left: 266px; right: 0; bottom: 0; height: 47px;
    background: var(--mosaic);
    clip-path: polygon(20px 0, 100% 0, 100% 100%, 0 100%);
  }
  .card--back .tagline { right: 34px; bottom: 17px; color: #fff; font-size: 12px; }
</style>
</head>
<body>

<section class="card card--front" aria-label="Card front">
  <div class="brand">
    <span class="brand__dot"></span>
    <span class="brand__name">VORNAK SYSTEMS</span>
  </div>
  <p class="tagline">A VORNAK GROUP DIVISION.</p>
  <div class="mosaic-disc" role="img" aria-label="Colourful low-poly mosaic pattern in green, cyan, yellow, orange, red and violet"></div>
</section>

<section class="card card--back" aria-label="Card back">
  <div class="brand">
    <span class="brand__dot"></span>
    <span class="brand__name">VORNAK SYSTEMS</span>
  </div>

  <p class="person">Rajesh Pallival</p>

  <ul class="contacts contacts--phones">
    <li>
      <svg viewBox="0 0 16 16" aria-hidden="true"><rect x="4" y="1" width="8" height="14" rx="1.5" fill="none" stroke="#c8161d" stroke-width="1.6"/><circle cx="8" cy="12.3" r="0.9" fill="#c8161d"/></svg>
      0097150738265
    </li>
    <li>
      <svg viewBox="0 0 16 16" aria-hidden="true"><circle cx="8" cy="8" r="6.8" fill="none" stroke="#c8161d" stroke-width="1.4"/><path d="M5.4 4.6l1.3-.3.8 1.9-.9.7a5 5 0 0 0 2.5 2.5l.7-.9 1.9.8-.3 1.3c-3.2.3-6.3-2.8-6-6z" fill="#c8161d"/></svg>
      009714368547
    </li>
  </ul>

  <ul class="contacts contacts--web">
    <li>
      <svg viewBox="0 0 16 16" aria-hidden="true"><rect x="1.5" y="3.5" width="13" height="9" fill="none" stroke="#c8161d" stroke-width="1.4"/><path d="M1.5 3.5L8 9l6.5-5.5" fill="none" stroke="#c8161d" stroke-width="1.4"/></svg>
      rajesh@vornaksys.example
    </li>
    <li>
      <svg viewBox="0 0 16 16" aria-hidden="true"><circle cx="8" cy="8" r="6.5" fill="none" stroke="#c8161d" stroke-width="1.4"/><ellipse cx="8" cy="8" rx="2.8" ry="6.5" fill="none" stroke="#c8161d" stroke-width="1.2"/><path d="M1.5 8h13M2.5 4.8h11M2.5 11.2h11" stroke="#c8161d" stroke-width="1.1"/></svg>
      www.vornaksys.example
    </li>
  </ul>

  <div class="footer-band" role="img" aria-label="Colourful low-poly mosaic strip"></div>
  <p class="tagline">A VORNAK GROUP DIVISION.</p>
</section>

</body>
</html>
```